Modern card design needed for building development company

We are looking for a sharp modern new look for our business cards.
We are a New Zealand based company called TKR Ventures NZ LTD that specialises in subdividing large sections, housing and commercial buildings.
We have attached a photo of the current logo and would like to see it improved somehow as it looks a bit dated.
We are open to any colours.

Target Market(s)

Investors, Property buyers

Industry/Entity Type

Investment

Contact Information for Business Card

TKR VENTURES NZ LTD
www.tkrventuresnz.co.nz

Damon Whitcombe
Phone +64 21 938 104
Email dpwhitcombe@korumail.co.nz

Font styles to use
Serif
Sans Serif

Colors
0792cd
33a6d7
85cae6
6b449b
886aae
f04a50
ec1f27
f37122
f68d4d

Requirements
Must have
• Please try and make the logo more modern or if you have a similar one we would like to see it.

```html
<!DOCTYPE html>
<html lang="en">
<head>
<meta charset="utf-8">
<title>TKR Ventures NZ LTD – Business Card</title>
<link rel="stylesheet" href="https://fonts.googleapis.com/css2?family=Oswald:wght@600&family=Open+Sans:wght@400&display=swap">
<style>
  :root {
    --purple: #6b449b;
    --purple-light: #886aae;
    --blue: #33a6d7;
    --blue-deep: #0792cd;
    --ink: #2b2b2b;
    --muted: #3a3a3a;
    --paper: #ffffff;
    --stage: #2a2a2c;
  }
  * { box-sizing: border-box; margin: 0; padding: 0; }
  html, body { width: 1200px; height: 900px; overflow: hidden; }
  body {
    background: var(--stage);
    font-family: "Open Sans", sans-serif;
    position: relative;
  }
  .card {
    position: absolute;
    left: 250px;
    width: 700px;
    height: 400px;
    background: var(--paper);
    overflow: hidden;
  }
  .card--front { top: 35px; }
  .card--back { top: 465px; }

  /* Front */
  .edge { position: absolute; top: 0; bottom: 0; width: 10px; }
  .edge--left { left: 0; background: var(--purple); }
  .edge--right { right: 0; background: var(--blue); }
  .front-brand {
    position: absolute; inset: 0;
    display: flex; flex-direction: column; align-items: center; justify-content: center;
    gap: 14px;
  }
  .brand-row { display: flex; align-items: center; gap: 14px; }
  .brand-mark { width: 34px; height: 34px; background: var(--purple); }
  .brand-name {
    font-family: "Oswald", sans-serif;
    font-weight: 600;
    font-size: 40px;
    letter-spacing: 0.5px;
    color: var(--ink);
  }
  .front-web { font-size: 26px; letter-spacing: 1px; color: var(--ink); }

  /* Back */
  .back-mark {
    position: absolute;
    left: 228px; top: 34px;
    width: 152px; height: 152px;
    background: var(--purple-light);
  }
  .band-line { position: absolute; left: 0; right: 0; height: 4px; background: var(--blue); }
  .band-line--top { top: 192px; }
  .band-line--bottom { top: 282px; }
  .band {
    position: absolute; left: 0; right: 0; top: 202px; height: 74px;
    background: var(--purple);
    display: flex; align-items: center; justify-content: center;
  }
  .band .brand-name { color: var(--paper); font-size: 40px; }
  .contacts {
    position: absolute; left: 70px; right: 40px; top: 302px;
    display: flex; flex-direction: column; gap: 8px;
    font-size: 17px; color: var(--muted);
  }
  .contact-line { display: flex; align-items: center; gap: 10px; line-height: 1.3; }
  .contact-line svg { width: 16px; height: 16px; flex: none; }
  .divider { margin: 0 12px; color: var(--muted); }
</style>
</head>
<body>

<section class="card card--front" aria-label="Business card front">
  <div class="edge edge--left"></div>
  <div class="edge edge--right"></div>
  <div class="front-brand">
    <div class="brand-row">
      <span class="brand-mark"></span>
      <span class="brand-name">TKR VENTURES NZ LTD</span>
    </div>
    <p class="front-web">www.tkrventuresnz.co.nz</p>
  </div>
</section>

<section class="card card--back" aria-label="Business card back">
  <span class="back-mark"></span>
  <div class="band-line band-line--top"></div>
  <div class="band">
    <span class="brand-name">TKR VENTURES NZ LTD</span>
  </div>
  <div class="band-line band-line--bottom"></div>

  <div class="contacts">
    <p class="contact-line">
      <svg viewBox="0 0 16 16" aria-hidden="true"><path d="M4 1.5l2.5 3-1.5 1.6a9 9 0 0 0 4.9 4.9L11.5 9.5l3 2.5-1.6 2.3C7.5 14.5 1.5 8.5 1.7 3.1z" fill="var(--blue)"/></svg>
      +64 21 938 104
    </p>
    <p class="contact-line">
      <svg viewBox="0 0 16 16" aria-hidden="true"><rect x="1" y="3" width="14" height="10" fill="var(--blue)"/><path d="M1 3.5l7 5.5 7-5.5" fill="none" stroke="#fff" stroke-width="1.2"/></svg>
      dpwhitcombe@korumail.co.nz
      <span class="divider">|</span>
      <svg viewBox="0 0 16 16" aria-hidden="true"><circle cx="8" cy="8" r="7" fill="var(--blue)"/><path d="M1 8h14M8 1c-3 3.5-3 10.5 0 14M8 1c3 3.5 3 10.5 0 14" fill="none" stroke="#fff" stroke-width="1"/></svg>
      www.tkrventuresnz.co.nz
    </p>
    <p class="contact-line">
      <svg viewBox="0 0 16 16" aria-hidden="true"><path d="M8 15s5-5.5 5-9A5 5 0 0 0 3 6c0 3.5 5 9 5 9z" fill="var(--blue)"/><circle cx="8" cy="6" r="1.8" fill="#fff"/></svg>
      PO BOX 48215, Harbourview, Auckland, New Zealand
    </p>
  </div>
</section>

</body>
</html>
```